MRT Property - Business Cards

Looking for a business card & general letterhead, signage etc design for our new logo.

Colours:
000a20
0056a2
00b5ef
0088ce
68cef2

Fonts:
Poppins
Karla

Please keep look and feel of new brand - example in the zip package I sent.

```html
<!DOCTYPE html>
<html lang="en">
<head>
<meta charset="utf-8">
<title>MRT Property – Letterhead</title>
<link rel="stylesheet" href="https://fonts.googleapis.com/css2?family=Poppins:wght@400;600&display=swap">
<style>
  :root {
    --ink: #000a20;
    --brand-deep: #0056a2;
    --brand-mid: #0088ce;
    --brand-bright: #00b5ef;
    --brand-soft: #68cef2;
    --paper: #ffffff;
    --backdrop: #e9eaee;
  }
  * { box-sizing: border-box; margin: 0; padding: 0; }
  html, body {
    width: 1200px; height: 792px; overflow: hidden;
    background: var(--backdrop);
    font-family: "Poppins", sans-serif;
  }
  .canvas {
    position: relative; width: 1200px; height: 792px;
  }
  .letterhead {
    position: absolute; left: 338px; top: 26px;
    width: 524px; height: 740px;
    background: var(--paper);
    box-shadow: 0 2px 10px rgba(0,10,32,0.12);
  }
  .letterhead__brand {
    position: absolute; top: 34px; left: 0; right: 0;
    display: flex; justify-content: center; align-items: center; gap: 10px;
  }
  .brand__dot {
    width: 22px; height: 22px; border-radius: 50%;
    background: var(--brand-bright);
  }
  .brand__name {
    font-family: "Poppins", sans-serif;
    font-weight: 600; font-size: 30px; letter-spacing: 0.5px;
    color: var(--brand-deep);
  }
  .letterhead__footer {
    position: absolute; left: 26px; right: 24px; bottom: 26px;
    font-size: 10.6px; color: var(--ink);
  }
  .footer__address {
    display: flex; justify-content: center; align-items: center; gap: 7px;
    margin-bottom: 9px;
  }
  .footer__contacts {
    display: flex; justify-content: space-between; align-items: center;
  }
  .contact { display: flex; align-items: center; gap: 5px; white-space: nowrap; }
  .icon { width: 9px; height: 9px; flex: none; }
  .icon--pin { width: 8px; height: 11px; }
</style>
</head>
<body>
<div class="canvas">
  <main class="letterhead">
    <header class="letterhead__brand">
      <span class="brand__dot"></span>
      <span class="brand__name">MRT Property</span>
    </header>

    <footer class="letterhead__footer">
      <p class="footer__address">
        <svg class="icon icon--pin" viewBox="0 0 8 11" aria-hidden="true">
          <path d="M4 0.5a3.3 3.3 0 0 0-3.3 3.3C0.7 6.3 4 9 4 9s3.3-2.7 3.3-5.2A3.3 3.3 0 0 0 4 0.5z" fill="none" stroke="var(--brand-mid)" stroke-width="1"/>
          <circle cx="4" cy="3.8" r="1.2" fill="var(--brand-mid)"/>
          <path d="M1.5 10.3h5" stroke="var(--brand-mid)" stroke-width="0.9"/>
        </svg>
        Suite 4.12, Level 3, 18 Harbourline Road, Westmere Bay NSW 2390
      </p>
      <div class="footer__contacts">
        <span class="contact">
          <svg class="icon" viewBox="0 0 10 10" aria-hidden="true">
            <path d="M2.2 0.8l1.5 1.9-0.9 1.1c0.6 1.3 1.6 2.3 2.9 2.9l1.1-0.9 1.9 1.5-0.9 1.6C4.6 8.9 1.1 5.4 0.6 1.7z" fill="var(--brand-mid)"/>
          </svg>
          +61 2 5550 0187
        </span>
        <span class="contact">
          <svg class="icon" viewBox="0 0 10 10" aria-hidden="true">
            <rect x="0.6" y="2" width="8.8" height="6.4" rx="0.8" fill="none" stroke="var(--brand-mid)" stroke-width="1"/>
            <path d="M0.8 2.4L5 5.6l4.2-3.2" fill="none" stroke="var(--brand-mid)" stroke-width="1"/>
          </svg>
          info@mrtproperty.com.au
        </span>
        <span class="contact">
          <svg class="icon" viewBox="0 0 10 10" aria-hidden="true">
            <circle cx="5" cy="5" r="4.3" fill="none" stroke="var(--brand-mid)" stroke-width="1"/>
            <path d="M0.8 5h8.4M5 0.7c-2.4 2.6-2.4 6 0 8.6M5 0.7c2.4 2.6 2.4 6 0 8.6" fill="none" stroke="var(--brand-mid)" stroke-width="0.8"/>
          </svg>
          www.mrtproperty.com.au
        </span>
      </div>
    </footer>
  </main>
</div>
</body>
</html>
```